Modern book cover design

We are looking for a modern, powerful book cover for a general intrest book about how robots are going to take human jobs in the future.

The book title is "Gearstorm"

It also has a strap line "The end of human jobs and how robots will replace them"
Both the title and the strap line should be on the front cover

I have attached a number of book designs I like, and my author picture.
Updates

Reason: Some great submissions but none quite have that wow factor

Target Market(s)

This is a general intrest book, but the reader is likely to be male 30-50

Requirements
Must have
• -Title "Gearstorm"

-Strap-line "The end of human jobs and how robots will replace them"

-Be compliant with PressNook Cover Design Criteria(www.pressnook-example.com)

-Book size : 5.5 x 8.5 inches

-Spine size : 0.625 inches

-Must have one author picture on the back cover(attached)

-Must have the following author description on back cover:
"Tom Hale is a leading futurologist, technologist, inventor, and entrepreneur. With over twenty years of experience in technology and innovation, Tom has travelled the world seeking out and developing new technologies. As a leading voice on the challenges and benefits of tomorrow’s technology, he has advised some of the world’s leading institutions, including the Amber Hall, regarding technological preparations for the future. He is the recipient of the millennium entrepreneur of the year award and has appeared on numerous technology and philanthropy television programs, as well as presenting Steel Dawn Weekly on Robotics."

-Must have the following book description on back cover:
“Gearstorm is a look at the rapidly changing face of robotics and how it will revolutionize employment over the next thirty years. Tom Hale lays out the arguments in favor of and against the mechanization of our society, as well as the advantages and untold risks as we march into this ever-present future.”

-Must have the following quote on the back cover:
"A fascinating look into the future of robotics and their impact on humanity, be prepared to question when robots will replace you - Derek Lansford, Professor of Cybernetics at the University of Elmsworth”

-Example barcode

```html
<!DOCTYPE html>
<html lang="en">
<head>
<meta charset="utf-8">
<title>Gearstorm – Book Cover</title>
<link rel="stylesheet" href="https://fonts.googleapis.com/css2?family=Open+Sans:ital,wght@0,400;0,700;1,400&family=PT+Sans:wght@400;700&display=swap">
<style>
  :root {
    --paper: #ececec;
    --paper-light: #f4f4f4;
    --paper-shade: #e2e2e2;
    --ink: #111111;
    --frame: #555555;
    --photo-light: #b9b9b9;
    --photo-dark: #3a3a3a;
    --button-red: #e3201b;
    --button-glow: #ff6a5f;
    --button-base: #a8a8a8;
    --button-label: #ffffff;
  }
  * { margin: 0; padding: 0; box-sizing: border-box; }
  html, body { width: 1200px; height: 879px; overflow: hidden; background: var(--paper); }
  .cover {
    position: relative;
    width: 1200px;
    height: 879px;
    background:
      radial-gradient(ellipse at 30% 25%, var(--paper-light), transparent 60%),
      radial-gradient(ellipse at 80% 80%, var(--paper-shade), transparent 65%),
      var(--paper);
    color: var(--ink);
    font-family: "Open Sans", Arial, sans-serif;
  }

  /* Back cover */
  .author-bio {
    position: absolute;
    left: 53px;
    top: 50px;
    width: 474px;
    font-size: 13.3px;
    line-height: 18.7px;
    letter-spacing: 0.25px;
  }
  .author-photo {
    float: left;
    width: 132px;
    height: 156px;
    margin: 1px 8px 2px -2px;
    background: radial-gradient(ellipse at 45% 40%, var(--photo-light), var(--photo-dark) 80%);
  }
  .book-description {
    position: absolute;
    left: 53px;
    top: 352px;
    width: 480px;
    font-size: 12.6px;
    font-weight: 700;
    line-height: 22px;
    letter-spacing: 0.2px;
  }
  .review {
    position: absolute;
    left: 53px;
    top: 661px;
    width: 482px;
    font-size: 12.6px;
    line-height: 21.5px;
    letter-spacing: 0.2px;
  }
  .review-quote { font-weight: 700; }
  .review-source { font-style: italic; padding-left: 51px; }
  .barcode-area {
    position: absolute;
    left: 440px;
    top: 792px;
    width: 104px;
    height: 61px;
    background: #ffffff;
    border: 1px solid var(--frame);
  }

  /* Spine */
  .spine-author, .spine-title {
    position: absolute;
    writing-mode: vertical-rl;
    transform: rotate(180deg);
    white-space: nowrap;
  }
  .spine-author {
    left: 580px;
    top: 197px;
    font-family: "PT Sans", Arial, sans-serif;
    font-size: 32px;
    line-height: 38px;
  }
  .spine-title {
    left: 566px;
    top: 374px;
    font-size: 56px;
    line-height: 60px;
    letter-spacing: 1.5px;
  }

  /* Front cover */
  .strapline {
    position: absolute;
    left: 664px;
    top: 33px;
    font-family: "PT Sans", Arial, sans-serif;
    font-size: 19.3px;
    white-space: nowrap;
    text-shadow: 1px 1px 1px rgba(0,0,0,0.25);
  }
  .front-title {
    position: absolute;
    left: 662px;
    top: 640px;
    font-size: 79px;
    font-weight: 400;
    line-height: 92px;
    white-space: nowrap;
    text-shadow: 2px 2px 2px rgba(0,0,0,0.25);
  }
  .push-button {
    position: absolute;
    left: 1060px;
    top: 749px;
    width: 96px;
    height: 80px;
    background:
      radial-gradient(ellipse 46% 40% at 50% 36%, var(--button-glow), var(--button-red) 70%, transparent 100%),
      radial-gradient(ellipse 50% 30% at 50% 74%, var(--button-base), transparent 100%);
  }
  .push-label {
    position: absolute;
    left: 0;
    top: 18px;
    width: 100%;
    text-align: center;
    font-size: 14px;
    font-weight: 700;
    color: var(--button-label);
  }
</style>
</head>
<body>
<main class="cover">
  <section class="back-cover">
    <div class="author-bio">
      <div class="author-photo" role="img" aria-label="Black and white portrait photo of the author Tom Hale"></div>
      Tom Hale is a leading futurologist, technologist, inventor, and entrepreneur. With over twenty years of experience in technology and innovation, Tom has travelled the world seeking out and developing new technologies. As a leading voice on the challenges and benefits of tomorrow’s technology, he has advised some of the world’s leading institutions, including the Amber Hall, regarding technological preparations for the future. He is the recipient of the millennium entrepreneur of the year award and has appeared on numerous technology and philanthropy television programs, as well as presenting Steel Dawn Weekly on Robotics.
    </div>

    <p class="book-description">Gearstorm is a look at the rapidly changing face of robotics and how it will revolutionize employment over the next thirty years. Tom Hale lays out the arguments in favor of and against the mechanization of our society, as well as the advantages and untold risks as we march into this ever-present future.</p>

    <blockquote class="review">
      <p class="review-quote">"A fascinating look into the future of robotics and their impact on humanity, be prepared to question when robots will replace you "</p>
      <p class="review-source">Derek Lansford, Professor of Cybernetics at the University of Elmsworth.</p>
    </blockquote>

    <div class="barcode-area" aria-hidden="true"></div>
  </section>

  <section class="spine">
    <div class="spine-title">Gearstorm</div>
    <div class="spine-author">Tom Hale</div>
  </section>

  <section class="front-cover">
    <p class="strapline">The end of human jobs and how robots will replace them..</p>
    <h1 class="front-title">Gearstorm</h1>
    <div class="push-button" role="img" aria-label="Illustration of a glossy red push button labelled PUSH">
      <span class="push-label">PUSH</span>
    </div>
  </section>
</main>
</body>
</html>
```